Business Card Design for company

We want new business cards. We'd like something different-- yet still highly professional. Our tagline is Providing leadership, delivering success. Stock photos are ok, as long as they are relevant and look upscale.

Target Market(s)

Architecture/Business Management Consulting/Engineering Consulting

Contact Information for Business Card

dark gray background with pops of blue might be good, but you tell me. You're the designers. Rounded corners might be nice, but again, you tell me.

Font styles to use
Serif
Sans Serif

Colors
3276b5
5c5c5c
9d9d9d
fbfbfb

Requirements
Nice to have
• Something different, but still very professional.

```html
<!DOCTYPE html>
<html lang="en">
<head>
<meta charset="utf-8">
<title>Harlow Group – Business Card</title>
<link href="https://fonts.googleapis.com/css2?family=Montserrat:wght@600;700&family=Work+Sans:wght@400;500&display=swap" rel="stylesheet">
<style>
  :root {
    --brand-blue: #2f6aa3;
    --brand-blue-light: #3276b5;
    --ink-dark: #4a4d55;
    --ink-mid: #5c5c5c;
    --ink-soft: #9d9d9d;
    --paper: #fbfbfb;
    --backdrop: #a9a9a9;
  }
  * { box-sizing: border-box; margin: 0; padding: 0; }
  html, body { width: 1200px; height: 930px; overflow: hidden; }
  body {
    background: radial-gradient(circle at 55% 30%, #c4c4c4 0%, var(--backdrop) 70%);
    font-family: "Work Sans", sans-serif;
    position: relative;
  }
  .card {
    position: absolute;
    width: 560px;
    height: 320px;
    box-shadow: 0 10px 24px rgba(0,0,0,0.3);
    overflow: hidden;
  }

  /* Back side */
  .card--back {
    left: 80px; top: 90px;
    background: linear-gradient(135deg, var(--brand-blue-light) 0%, var(--brand-blue) 100%);
    color: var(--paper);
  }
  .card--back .wordmark {
    position: absolute; left: 0; right: 0; top: 110px;
    text-align: center;
    font-family: "Montserrat", sans-serif;
    font-weight: 700;
    font-size: 44px;
    letter-spacing: 3px;
  }
  .card--back .web-rule {
    position: absolute; left: 70px; right: 70px; top: 232px;
    display: flex; align-items: center; gap: 12px;
    font-size: 13px; letter-spacing: 0.5px;
  }
  .card--back .web-rule::before,
  .card--back .web-rule::after {
    content: ""; flex: 1; height: 1px; background: rgba(251,251,251,0.6);
  }

  /* Front side */
  .card--front {
    left: 560px; top: 500px;
    background: var(--paper);
    color: var(--ink-mid);
  }
  .card--front .wordmark {
    position: absolute; right: 40px; top: 44px;
    font-family: "Montserrat", sans-serif;
    font-weight: 700;
    font-size: 30px;
    letter-spacing: 2px;
    color: var(--brand-blue);
  }
  .card--front .top-rule {
    position: absolute; left: 170px; right: 40px; top: 128px;
    height: 1.5px; background: var(--brand-blue);
  }
  .address {
    position: absolute; right: 40px; top: 142px;
    text-align: right; font-size: 13px; line-height: 1.5;
    color: var(--ink-mid);
  }
  .person {
    position: absolute; left: 40px; top: 150px;
  }
  .person__name {
    font-family: "Montserrat", sans-serif;
    font-weight: 600; font-size: 21px;
    color: var(--brand-blue); letter-spacing: 0.5px;
  }
  .person__role { font-size: 12px; margin-top: 2px; padding-left: 18px; }
  .person-rule {
    position: absolute; left: 58px; width: 280px; top: 212px;
    height: 1.5px; background: var(--brand-blue);
  }
  .contacts {
    position: absolute; left: 58px; top: 224px;
    list-style: none; font-size: 14px; line-height: 22px;
  }
  .contacts li { display: flex; align-items: center; gap: 8px; }
  .contacts svg { width: 10px; height: 10px; fill: none; stroke: var(--brand-blue); stroke-width: 1.6; }
  .contacts .accent { color: var(--brand-blue); }
  .base-band {
    position: absolute; left: 0; right: 0; bottom: 0; height: 9px;
    display: flex;
  }
  .base-band__blue { flex: 0 0 60%; background: var(--brand-blue); }
  .base-band__grey { flex: 1; background: var(--ink-dark); }
</style>
</head>
<body>
  <section class="card card--back" aria-label="Card back">
    <div class="wordmark">HARLOW GROUP</div>
    <div class="web-rule">www.harlowgroup.com</div>
  </section>

  <section class="card card--front" aria-label="Card front">
    <div class="wordmark">HARLOW GROUP</div>
    <div class="top-rule"></div>
    <address class="address">58b Calder Street,<br>Westfield, NZ, 4021</address>
    <div class="person">
      <div class="person__name">DANIEL REEVE</div>
      <div class="person__role">Director</div>
    </div>
    <div class="person-rule"></div>
    <ul class="contacts">
      <li><svg viewBox="0 0 10 10"><path d="M2 1 L4 3 L3 4 Q4.5 6 6 7 L7 6 L9 8 L8 9 Q4 9 1 2 Z"/></svg>(555) 014-2290</li>
      <li><svg viewBox="0 0 10 10"><rect x="1" y="2.5" width="8" height="5.5"/><path d="M1 2.5 L5 5.5 L9 2.5"/></svg>info@harlowgroup.com</li>
      <li><svg viewBox="0 0 10 10"><circle cx="5" cy="5" r="4"/><path d="M1 5 H9 M5 1 Q2.5 5 5 9 M5 1 Q7.5 5 5 9"/></svg>www.<span class="accent">harlowgroup</span>.com</li>
    </ul>
    <div class="base-band"><div class="base-band__blue"></div><div class="base-band__grey"></div></div>
  </section>
</body>
</html>
```